We are a recruitment company based in Norwich/Cambridge England.
I have included our company logo which we want to remain the same.

What we are looking for is a new creative Business card which will really stand out!!

Contact Information for Business Card

Harriet Dunmore
email: Harriet@plavex.co.uk
Address: Brackwell House
Fenmoor Enterprise Park
Partridge Way
Norwich
QB9 3KX
Tel:01632 960418

```html
<!DOCTYPE html>
<html lang="en">
<head>
<meta charset="utf-8">
<title>Plavex Business Card</title>
<link rel="stylesheet" href="https://fonts.googleapis.com/css2?family=Open+Sans:wght@400;600;700&display=swap">
<style>
  :root {
    --page: #ece9e4;
    --card-white: #f7f7f5;
    --green: #8cc63f;
    --green-light: #a6d452;
    --band-grey: #b5b4b9;
    --logo-grey: #8a898e;
    --back-grey: #8f8e94;
    --back-pattern: #9b9aa0;
    --white: #ffffff;
    --font: "Open Sans", Arial, sans-serif;
  }
  * { margin: 0; padding: 0; box-sizing: border-box; }
  html, body { width: 1200px; height: 780px; overflow: hidden; }
  body { background: var(--page); font-family: var(--font); position: relative; }

  .card {
    position: absolute;
    width: 520px;
    height: 298px;
    border-radius: 3px;
    overflow: hidden;
    box-shadow: 0 10px 24px rgba(0,0,0,.18), 0 2px 4px rgba(0,0,0,.12);
  }
  .card--front { left: 50px; top: 241px; background: var(--card-white); }
  .card--back  { left: 630px; top: 241px; background: var(--back-grey); }

  .front-curves { position: absolute; inset: 0; }

  .brand { position: absolute; display: flex; align-items: center; gap: 12px; }
  .brand__mark { width: 44px; height: 44px; border-radius: 50%; flex: none; }
  .brand__name { font-weight: 700; font-size: 44px; line-height: 1; letter-spacing: -1px; }
  .brand__tagline { font-size: 9px; letter-spacing: 2px; margin-top: 6px; font-weight: 600; }

  .brand--front { left: 34px; top: 104px; }
  .brand--front .brand__mark { background: var(--green); }
  .brand--front .brand__name { color: var(--green); }
  .brand--front .brand__tagline { color: var(--logo-grey); }

  .contact {
    position: absolute;
    right: 24px;
    top: 26px;
    text-align: right;
    color: var(--white);
  }
  .contact__name { font-size: 20px; font-weight: 700; line-height: 1.1; }
  .contact__role { font-size: 12px; margin-bottom: 16px; }
  .contact__list { list-style: none; }
  .contact__item {
    display: flex; justify-content: flex-end; align-items: center;
    gap: 8px; font-size: 11.5px; line-height: 1; margin-bottom: 9px;
  }
  .contact__icon { width: 16px; height: 16px; flex: none; }

  .address {
    position: absolute;
    right: 24px;
    bottom: 22px;
    text-align: right;
    color: var(--white);
    font-size: 11.5px;
    line-height: 1.5;
  }

  .back-pattern { position: absolute; inset: 0; background: radial-gradient(circle at 50% 50%, var(--back-pattern), var(--back-grey)); }
  .brand--back { left: 50%; top: 92px; transform: translateX(-50%); }
  .brand--back .brand__mark { background: var(--white); width: 52px; height: 52px; }
  .brand--back .brand__name { color: var(--white); font-size: 52px; }
  .brand--back .brand__tagline { color: var(--white); }
  .back-web {
    position: absolute; left: 0; right: 0; top: 216px;
    text-align: center; color: var(--white);
    font-size: 13px; letter-spacing: 3px;
  }
</style>
</head>
<body>

<section class="card card--front" aria-label="Business card front">
  <svg class="front-curves" viewBox="0 0 520 298" aria-hidden="true">
    <path d="M246 0 C300 110 300 210 226 298 L520 298 L520 0 Z" fill="var(--band-grey)"/>
    <path d="M262 0 C318 110 318 210 246 298 L520 298 L520 0 Z" fill="var(--card-white)"/>
    <path d="M268 0 C324 110 324 210 252 298 L520 298 L520 0 Z" fill="var(--green)"/>
    <path d="M300 0 C340 80 340 160 310 230 C400 150 470 70 520 0 Z" fill="var(--green-light)" opacity=".45"/>
  </svg>

  <div class="brand brand--front">
    <span class="brand__mark"></span>
    <div>
      <div class="brand__name">Plavex</div>
      <div class="brand__tagline">Technology Recruitment</div>
    </div>
  </div>

  <div class="contact">
    <div class="contact__name">Harriet Dunmore</div>
    <div class="contact__role">CEO</div>
    <ul class="contact__list">
      <li class="contact__item">01632 960418
        <svg class="contact__icon" viewBox="0 0 16 16"><circle cx="8" cy="8" r="7" fill="none" stroke="#fff" stroke-width="1.2"/><rect x="5.5" y="4" width="5" height="8" rx="1" fill="none" stroke="#fff" stroke-width="1.1"/></svg>
      </li>
      <li class="contact__item">Harriet@plavex.co.uk
        <svg class="contact__icon" viewBox="0 0 16 16"><circle cx="8" cy="8" r="7" fill="none" stroke="#fff" stroke-width="1.2"/><rect x="4.5" y="5.5" width="7" height="5" fill="none" stroke="#fff" stroke-width="1"/><path d="M4.5 5.5 L8 8.5 L11.5 5.5" fill="none" stroke="#fff" stroke-width="1"/></svg>
      </li>
      <li class="contact__item">www.plavex.co.uk
        <svg class="contact__icon" viewBox="0 0 16 16"><circle cx="8" cy="8" r="7" fill="none" stroke="#fff" stroke-width="1.2"/><circle cx="8" cy="8" r="3.8" fill="none" stroke="#fff" stroke-width="1"/><path d="M4.2 8 H11.8 M8 4.2 V11.8" stroke="#fff" stroke-width="1"/></svg>
      </li>
      <li class="contact__item">Brackwell House
        <svg class="contact__icon" viewBox="0 0 16 16"><circle cx="8" cy="8" r="7" fill="none" stroke="#fff" stroke-width="1.2"/><path d="M8 12 C6 9.5 5.5 8.5 5.5 7 A2.5 2.5 0 0 1 10.5 7 C10.5 8.5 10 9.5 8 12 Z" fill="#fff"/></svg>
      </li>
    </ul>
  </div>

  <address class="address" style="font-style: normal;">
    Fenmoor Enterprise Park<br>
    Partridge Way, Norwich QB9 3KX
  </address>
</section>

<section class="card card--back" aria-label="Business card back">
  <div class="back-pattern" role="img" aria-label="Faint repeating brand pattern in soft grey tones"></div>
  <div class="brand brand--back">
    <span class="brand__mark"></span>
    <div>
      <div class="brand__name">Plavex</div>
      <div class="brand__tagline">Technology Recruitment</div>
    </div>
  </div>
  <div class="back-web">www.plavex.co.uk</div>
</section>

</body>
</html>
```